New Bicycle shop business card

Hi!
I'm looking for a business card for my new proffesional bike mechanics shop. This shop is only for fixing broken bikes and not selling bikes.
Peferbly a modern and sleek and modern design.
Colors: black, grey, red, white
Information:
Name: Rijwielwerkplaats Vanhoutte
Shop owner: Bart Vanhoutte & Marieke Segers
Website: www.rijwielwerkplaats-vanhoutte.be
Email: info@rijwielwerkplaats-vanhoutte.be
Phone number: +32471902368
Street adres: Kerkweg 46
9940 Bellebeke
Slogan/shop information: Herstellingen van alle merken.
Logo: see files.
Target Market(s)
People who seek a mechanic to fix or upgrade their bikes.
Contact Information for Business Card
Information:
Website: info@rijwielwerkplaats-vanhoutte.be
9940 Bellebeke
Logo: see files.

```html
<!DOCTYPE html>
<html lang="nl">
<head>
<meta charset="utf-8">
<title>Rijwielwerkplaats Vanhoutte – visitekaartje</title>
<link rel="stylesheet" href="https://fonts.googleapis.com/css2?family=Source+Sans+3:wght@400;600;700&display=swap">
<style>
  :root {
    --black: #151515;
    --frame: #1c1c1c;
    --white: #ffffff;
    --paper: #f6f6f6;
    --grey: #9a9c9b;
    --red: #e0203f;
    --ink: #1a1a1a;
    --backdrop: #4a4a4a;
  }
  * { box-sizing: border-box; margin: 0; padding: 0; }
  html, body { width: 1200px; height: 1021px; overflow: hidden; }
  body {
    background: var(--backdrop);
    font-family: "Source Sans 3", sans-serif;
    position: relative;
  }
  .card {
    position: absolute;
    left: 220px;
    width: 760px;
    height: 434px;
  }
  /* back side */
  .card-back {
    top: 52px;
    background: var(--black);
    color: var(--white);
    text-align: center;
  }
  .brand {
    position: absolute;
    left: 0; right: 0;
    display: flex;
    flex-direction: column;
    align-items: center;
  }
  .brand-dot {
    width: 54px; height: 54px;
    border-radius: 50%;
    background: var(--red);
    margin-bottom: 18px;
  }
  .brand-name {
    font-weight: 700;
    text-transform: uppercase;
    letter-spacing: 0.06em;
    line-height: 1.05;
  }
  .card-back .brand { top: 120px; }
  .card-back .brand-name { font-size: 34px; color: var(--white); }
  .slogan {
    position: absolute;
    left: 0; right: 0; top: 296px;
    font-size: 19px;
    letter-spacing: 0.04em;
  }
  /* front side */
  .card-front {
    top: 535px;
    background: var(--frame);
    padding: 14px;
  }
  .front-inner {
    position: relative;
    width: 100%; height: 100%;
    background: linear-gradient(180deg, var(--white), var(--paper));
    overflow: hidden;
  }
  .gear-corner { position: absolute; width: 56px; height: 56px; }
  .gear-corner.tl { top: 0; left: 0; }
  .gear-corner.tr { top: 0; right: 0; transform: scaleX(-1); }
  .gear-corner.bl { bottom: 0; left: 0; transform: scaleY(-1); }
  .gear-corner.br { bottom: 0; right: 0; transform: scale(-1, -1); }
  .card-front .brand { top: 44px; }
  .card-front .brand-dot { width: 48px; height: 48px; margin-bottom: 14px; }
  .card-front .brand-name { font-size: 31px; color: var(--ink); }
  .details {
    position: absolute;
    top: 196px; left: 0; right: 0;
    display: flex;
    justify-content: center;
  }
  .people {
    text-align: right;
    padding-right: 18px;
    padding-top: 4px;
  }
  .people-names { color: var(--red); font-size: 21px; font-weight: 600; }
  .people-role { color: var(--ink); font-size: 19px; margin-top: 2px; }
  .divider { width: 1px; background: #9a9a9a; height: 80px; }
  .contact { list-style: none; padding-left: 16px; font-size: 18px; color: var(--ink); }
  .contact li { display: flex; align-items: center; gap: 8px; line-height: 1.4; }
  .contact svg { width: 15px; height: 15px; flex: none; }
  .address {
    position: absolute;
    top: 318px; left: 0; right: 0;
    text-align: center;
    font-size: 20px;
    color: var(--ink);
  }
</style>
</head>
<body>

<section class="card card-back" aria-label="Achterkant visitekaartje">
  <div class="brand">
    <span class="brand-dot"></span>
    <p class="brand-name">Rijwielwerkplaats Vanhoutte</p>
  </div>
  <p class="slogan">Herstellingen van alle merken.</p>
</section>

<section class="card card-front" aria-label="Voorkant visitekaartje">
  <div class="front-inner">
    <svg class="gear-corner tl" viewBox="0 0 56 56" role="img" aria-label="Tandwiel-hoekornament"><path d="M0 0H56A56 56 0 0 1 0 56Z" fill="var(--grey)"/></svg>
    <svg class="gear-corner tr" viewBox="0 0 56 56" role="img" aria-label="Tandwiel-hoekornament"><path d="M0 0H56A56 56 0 0 1 0 56Z" fill="var(--grey)"/></svg>
    <svg class="gear-corner bl" viewBox="0 0 56 56" role="img" aria-label="Tandwiel-hoekornament"><path d="M0 0H56A56 56 0 0 1 0 56Z" fill="var(--grey)"/></svg>
    <svg class="gear-corner br" viewBox="0 0 56 56" role="img" aria-label="Tandwiel-hoekornament"><path d="M0 0H56A56 56 0 0 1 0 56Z" fill="var(--grey)"/></svg>

    <div class="brand">
      <span class="brand-dot"></span>
      <p class="brand-name">Rijwielwerkplaats Vanhoutte</p>
    </div>

    <div class="details">
      <div class="people">
        <p class="people-names">Bart Vanhoutte &amp; Marieke Segers</p>
        <p class="people-role">Shop Owner</p>
      </div>
      <div class="divider"></div>
      <ul class="contact">
        <li>
          <svg viewBox="0 0 16 16" aria-hidden="true"><path d="M3.5 1.5l2.5 0 1 3.5-1.8 1.2a8 8 0 0 0 4.6 4.6L11 9l3.5 1v2.5a2 2 0 0 1-2 2A11 11 0 0 1 1.5 3.5a2 2 0 0 1 2-2z" fill="var(--red)"/></svg>
          +32471902368
        </li>
        <li>
          <svg viewBox="0 0 16 16" aria-hidden="true"><rect x="1.5" y="3.5" width="13" height="9" fill="none" stroke="var(--red)" stroke-width="1.6"/><path d="M1.5 3.5L8 9l6.5-5.5" fill="none" stroke="var(--red)" stroke-width="1.6"/></svg>
          info@rijwielwerkplaats-vanhoutte.be
        </li>
        <li>
          <svg viewBox="0 0 16 16" aria-hidden="true"><circle cx="8" cy="8" r="6.5" fill="none" stroke="var(--red)" stroke-width="1.4"/><ellipse cx="8" cy="8" rx="3" ry="6.5" fill="none" stroke="var(--red)" stroke-width="1.2"/><path d="M1.5 8h13M2.5 5h11M2.5 11h11" stroke="var(--red)" stroke-width="1.1"/></svg>
          www.rijwielwerkplaats-vanhoutte.be
        </li>
      </ul>
    </div>

    <p class="address">Kerkweg 46, 9940 Bellebeke</p>
  </div>
</section>

</body>
</html>
```